Property Finance Company - Orbin Funding Limited

Background: Orbin Funding Group Limited is a private property finance company. Orbin Funding Group has capital to directly fund first mortgage, mezzanine and preferred equity financing. We also acquire performing, sub-performing and distressed debt.

Orbin Fundings management philosophy emphasises expertise, innovation, wisdom, honesty and competitiveness. Orbin Funding are not finance brokers - we provide debt funding to the commercial property and residential development sectors. Our process is built from experience and cumutavely Orbin Fundings Directors have in excess of 60 years wisdom.

The aim of the website will be to increase brand awareness, provide clients with comfort around our level of skill and background on who we are, generate more sales, and provide examples of projects that we have funded.

The website is a new product launch, and we need to use our Orbin Funding logo that has just been designed. We like a dark background, and either black/silver/grey/ jade green, or black/gold/jade green colours.

Our unique advantages are that we have fast turnaround times, we can solve clients funding problems and we know what we are doing. Our target audience will be viewing the website on both desktop and mobile devices.

We would like to have the following pages:

Home
About
Team
Services
Project Experience
Contact

Competitors Website: http://www.tarvolo.example/

We would also like to have the option of video footage in our website, as you can see in our competitors website.

Overall we want a really slick, elegant but modern website that is better than www.tarvolo.example

Target Market(s)

Finance borrowers, property developers, accountants, lawyers, businesspeople, high net worth people

Industry/Entity Type

Finance

Requirements
Must have
• Please see project description
Nice to have
Should not have

```html
<!DOCTYPE html>
<html lang="en">
<head>
<meta charset="utf-8">
<title>Orbin Funding Group</title>
<link href="https://fonts.googleapis.com/css2?family=Cinzel:wght@400;700&family=Open+Sans:wght@400;600;700&display=swap" rel="stylesheet">
<style>
:root{
  --green:#0ea36b;
  --green-dark:#08895a;
  --ink:#1d1d1d;
  --black:#111;
  --grey-bg:#ececec;
  --text:#555;
  --white:#fff;
  --field:#eeeeee;
  --footer:#1b1b1b;
}
*{box-sizing:border-box;margin:0;padding:0}
html,body{width:1200px;height:5202px;overflow:hidden}
body{position:relative;background:var(--white);font-family:"Open Sans",Arial,sans-serif;color:var(--text)}
.abs{position:absolute}
.section-title{position:absolute;left:0;width:1200px;text-align:center;font-family:"Cinzel",Georgia,serif;font-size:46px;color:var(--ink);letter-spacing:1px}
.section-text{position:absolute;left:200px;width:800px;text-align:center;font-size:14px;line-height:26px;color:var(--text)}

/* header */
.site-header{position:absolute;left:0;top:0;width:1200px;height:104px;background:var(--white)}
.brand{position:absolute;left:60px;top:22px;display:flex;align-items:center;gap:10px}
.brand-dot{width:48px;height:48px;border-radius:50%;background:#9a9a9a}
.brand-name{font-family:"Cinzel",Georgia,serif;font-size:15px;line-height:18px;color:#333;width:110px}
.main-nav{position:absolute;left:292px;top:36px;display:flex;align-items:center;gap:22px;font-size:15px;font-weight:600;color:#333}
.main-nav .active{background:var(--green);color:var(--white);padding:7px 26px;border-radius:20px}
.call{position:absolute;left:918px;top:26px;border-left:2px solid #ccc;padding-left:18px;display:flex;align-items:center;gap:14px}
.call small{display:block;font-size:13px;color:#333}
.call strong{display:block;font-size:26px;font-weight:600;color:#222}

/* hero */
.hero{position:absolute;left:0;top:104px;width:1200px;height:572px;background:linear-gradient(120deg,#3b3b3b 0%,#6a5e55 40%,#2a2a2a 70%,#4a4a48 100%)}
.hero-shade{position:absolute;inset:0;background:rgba(0,0,0,.35)}
.hero h1{position:absolute;top:160px;width:1200px;text-align:center;font-family:"Cinzel",Georgia,serif;font-size:58px;color:var(--white);font-weight:700}
.hero p{position:absolute;top:246px;left:350px;width:500px;text-align:center;font-size:17px;font-style:italic;line-height:26px;color:var(--white)}
.play{position:absolute;left:547px;top:330px}

/* welcome */
.welcome{position:absolute;left:0;top:676px;width:1200px;height:271px;background:var(--green)}
.welcome h2{position:absolute;top:54px;width:1200px;text-align:center;font-family:"Cinzel",Georgia,serif;font-size:44px;color:var(--ink)}
.welcome p{position:absolute;top:118px;left:140px;width:920px;text-align:center;font-size:14px;line-height:26px;color:var(--white)}
.welcome-arrow{position:absolute;left:580px;top:251px;width:40px;height:40px;border-radius:50%;background:var(--green);display:flex;align-items:flex-end;justify-content:center;padding-bottom:8px}

/* services */
.service{position:absolute;width:514px;height:257px;overflow:hidden}
.service .label{position:absolute;bottom:16px;left:0;width:100%;text-align:center;font-family:"Cinzel",Georgia,serif;font-size:17px;color:var(--white);letter-spacing:1px}
.service.featured{background:linear-gradient(135deg,#14b478,#0b9660)}
.service.featured h3{position:absolute;top:62px;width:100%;text-align:center;font-family:"Cinzel",Georgia,serif;font-size:24px;color:var(--white);font-weight:400}
.service.featured p{position:absolute;top:100px;left:80px;width:354px;text-align:center;font-size:14px;line-height:22px;color:var(--white)}
.service-hub{position:absolute;left:524px;top:1391px;width:152px;height:152px;border-radius:50%;background:var(--white);border:6px solid #ddd}
.service-hub span{position:absolute;left:36px;top:36px;width:68px;height:68px;border-radius:50%;background:#9b9b9b}

/* expertise */
.expertise{position:absolute;left:0;top:1810px;width:1200px;height:250px;background:var(--green)}
.expertise-tag{position:absolute;left:0;top:0}
.expertise-tag h2{position:absolute;left:76px;top:74px;font-family:"Cinzel",Georgia,serif;font-size:34px;line-height:46px;color:var(--white);font-weight:400}
.value{position:absolute;top:40px;width:180px;text-align:center}
.value .ring{width:90px;height:90px;margin:0 auto;border-radius:50%;border:3px solid var(--white);display:flex;align-items:center;justify-content:center;background:rgba(0,0,0,.1)}
.value span{display:block;margin-top:50px;font-family:"Cinzel",Georgia,serif;font-size:19px;color:var(--white)}

/* about */
.about{position:absolute;left:0;top:2067px;width:1200px;height:493px;background:var(--grey-bg)}
.about h2{position:absolute;left:76px;top:100px;font-family:"Cinzel",Georgia,serif;font-size:40px;color:var(--ink);font-weight:400}
.about p{position:absolute;left:76px;top:160px;width:530px;font-size:14px;line-height:25px;color:var(--text)}
.btn{position:absolute;background:var(--green);color:var(--white);border-radius:30px;text-align:center;font-family:"Cinzel",Georgia,serif;font-weight:700;letter-spacing:1px}
.about-photo{position:absolute;left:652px;top:63px;width:458px;height:353px;border:6px solid var(--white);background:linear-gradient(135deg,#d9d6d0,#b9b2a8 50%,#6c6660)}

/* projects */
.project{position:absolute;top:2785px;width:338px;height:409px}
.project .photo{width:100%;height:215px}
.project .body{height:194px;background:var(--green);text-align:center;padding-top:28px}
.project h3{font-family:"Cinzel",Georgia,serif;font-size:20px;color:var(--ink);font-weight:700}
.project p{margin:10px auto 0;width:270px;font-size:14px;line-height:22px;color:var(--white)}
.project .go{position:absolute;left:149px;top:384px}

/* clients */
.clients{position:absolute;left:0;top:3381px;width:1200px;height:624px;background:linear-gradient(180deg,#0ea36b,#0b9a63)}
.clients h2{position:absolute;top:50px;width:1200px;text-align:center;font-family:"Cinzel",Georgia,serif;font-size:44px;color:var(--ink);font-weight:400}
.quote-mark{position:absolute;left:562px;top:124px}
.clients blockquote{position:absolute;top:230px;left:170px;width:860px;text-align:center;font-size:15px;font-style:italic;line-height:27px;color:var(--white)}
.client-name{position:absolute;top:330px;width:1200px;text-align:center;font-size:16px;font-weight:700;color:var(--white);letter-spacing:1px}
.client-name::before{content:"";display:inline-block;width:30px;height:2px;background:var(--white);vertical-align:middle;margin-right:12px}

/* team */
.team{position:absolute;left:0;top:4005px;width:1200px;height:417px;background:linear-gradient(135deg,#2a2a2a,#111 50%,#262626)}
.team h2{position:absolute;left:76px;top:168px;font-family:"Cinzel",Georgia,serif;font-size:32px;line-height:46px;color:var(--white);font-weight:400}
.member{position:absolute;top:40px;width:190px}
.member .photo{width:150px;height:238px;margin:0 auto;background:linear-gradient(180deg,#4a4a4a,#2d3440)}
.member .tag{height:80px;background:var(--green);text-align:center;padding-top:14px}
.member .tag strong{display:block;font-family:"Cinzel",Georgia,serif;font-size:20px;color:var(--white);font-weight:400}
.member .tag span{display:block;margin-top:4px;font-size:12px;font-weight:700;color:var(--white)}

/* contact */
.field{position:absolute;background:var(--field);font-size:13px;color:#777;padding:15px 20px}

/* footer */
.site-footer{position:absolute;left:0;top:4925px;width:1200px;height:277px;background:var(--footer);border-top:8px solid var(--green)}
.footer-nav{position:absolute;left:76px;top:44px;display:flex;align-items:center;gap:20px;font-size:15px;color:var(--white)}
.footer-nav .active{background:var(--green);padding:5px 22px;border-radius:18px;font-weight:700}
.footer-nav i{font-style:normal;color:#888}
.social{position:absolute;left:964px;top:36px;display:flex;gap:12px}
.social span{width:40px;height:40px;border-radius:50%;border:2px solid #aaa}
.social span.on{background:var(--green);border-color:var(--green)}
.footer-divider{position:absolute;left:76px;top:110px;width:1048px;height:1px;background:#333}
.footer-contact h4{position:absolute;left:76px;top:128px;font-size:20px;font-weight:700;color:var(--white);letter-spacing:1px}
.info{position:absolute;top:182px;display:flex;align-items:center;gap:14px;font-size:14px;line-height:20px;color:var(--white)}
.info .pin{width:48px;height:48px;border-radius:50%;display:flex;align-items:center;justify-content:center;flex:none}
</style>
</head>
<body>

<header class="site-header">
  <div class="brand"><span class="brand-dot"></span><span class="brand-name">Orbin Funding Group</span></div>
  <nav class="main-nav"><span class="active">HOME</span><span>ABOUT</span><span>TEAM</span><span>SERVICES</span><span>PROJECT EXPERIENCE</span><span>CONTACT</span></nav>
  <div class="call">
    <svg width="34" height="34" viewBox="0 0 24 24"><path fill="#0ea36b" d="M6.6 10.8c1.4 2.8 3.8 5.1 6.6 6.6l2.2-2.2c.3-.3.7-.4 1-.2 1.1.4 2.3.6 3.6.6.6 0 1 .4 1 1V20c0 .6-.4 1-1 1C10.6 21 3 13.4 3 4c0-.6.4-1 1-1h3.5c.6 0 1 .4 1 1 0 1.3.2 2.5.6 3.6.1.3 0 .7-.2 1z"/></svg>
    <div><small>Call Us Today :</small><strong>123 456 7890</strong></div>
  </div>
</header>

<section class="hero" role="img" aria-label="Background video still of business people meeting in an office">
  <div class="hero-shade"></div>
  <h1>ORBIN FUNDING GROUP</h1>
  <p>Orbin Funding Group has capital to directly fund first mortgage, mezzanine and preferred equity financing</p>
  <svg class="play" width="106" height="106" viewBox="0 0 106 106"><circle cx="53" cy="53" r="49" fill="rgba(255,255,255,.25)" stroke="#fff" stroke-width="5"/><path d="M42 32 L76 53 L42 74 Z" fill="#fff"/></svg>
</section>

<section class="welcome">
  <h2>WELCOME TO ORBIN FUNDING GROUP</h2>
  <p>Lorem Ipsum is simply dummy text of the printing and typesetting industry. Lorem Ipsum has been the industry's standard dummy text ever since the 1500s, when an unknown printer took a galley of type and scrambled it to make a type specimen book. It has survived not only five centuries, but also the leap into electronic typesetting, remaining essentially unchanged.</p>
  <div class="welcome-arrow"><svg width="14" height="10" viewBox="0 0 14 10"><path d="M1 1 L7 8 L13 1" fill="none" stroke="#fff" stroke-width="2"/></svg></div>
</section>

<h2 class="section-title" style="top:1035px">SERVICES WE PROVIDE YOU</h2>
<p class="section-text" style="top:1100px">Lorem Ipsum is simply dummy text of the printing and typesetting industry. Lorem Ipsum has been the industry's standard dummy text ever since the 1500s, when an unknown printer took a galley of type and scrambled it to make</p>

<div class="service featured" style="left:76px;top:1200px">
  <h3>DEBT FUNDING</h3>
  <p>Lorem Ipsum is simply dummy text of the printing and typesetting industry. Lorem Ipsum has been the industry's standard dummy text</p>
  <svg class="abs" style="left:232px;top:196px" width="50" height="14" viewBox="0 0 50 14"><path d="M0 7 H46 M39 1 L47 7 L39 13" fill="none" stroke="#fff" stroke-width="2.5"/></svg>
</div>
<div class="service" style="left:614px;top:1200px;background:linear-gradient(160deg,#c8ccd3,#8e949c 60%,#5b5f66)" role="img" aria-label="Photo of a large steel-framed building under construction"><span class="label">MEZZANINE</span></div>
<div class="service" style="left:76px;top:1488px;background:linear-gradient(160deg,#e4e6ea,#9aa0a8 55%,#4e545c)" role="img" aria-label="Photo of city skyscrapers viewed from below"><span class="label">EQUITY FINANCING</span></div>
<div class="service" style="left:614px;top:1488px;background:linear-gradient(160deg,#cdd8e4,#6d86a2 55%,#2f3e52)" role="img" aria-label="Photo of a modern glass office building"><span class="label">PERFORMING</span></div>
<div class="service-hub"><span></span></div>

<section class="expertise">
  <svg class="expertise-tag" width="300" height="250" viewBox="0 0 300 250"><path d="M0 0 H210 L295 125 L210 250 H0 Z" fill="#0b0b0b"/></svg>
  <div class="expertise-tag"><h2>OUR<br>EXPERTISE</h2></div>
  <div class="value" style="left:333px"><div class="ring"><svg width="46" height="46" viewBox="0 0 46 46" fill="none" stroke="#fff" stroke-width="2.5"><path d="M23 8a11 11 0 0 0-6 20v5h12v-5a11 11 0 0 0-6-20zM18 37h10M20 41h6"/></svg></div><span>Innovation</span></div>
  <div class="value" style="left:527px"><div class="ring"><svg width="46" height="46" viewBox="0 0 46 46" fill="none" stroke="#fff" stroke-width="2.5"><path d="M8 16 L23 8 L38 16 Z M11 18v14M18 18v14M28 18v14M35 18v14M7 36h32"/></svg></div><span>Wisdom</span></div>
  <div class="value" style="left:725px"><div class="ring"><svg width="46" height="46" viewBox="0 0 46 46" fill="none" stroke="#fff" stroke-width="2.5"><circle cx="23" cy="13" r="6"/><path d="M12 40v-10a11 11 0 0 1 22 0v10M17 28l6 6 6-6"/></svg></div><span>Honesty</span></div>
  <div class="value" style="left:923px"><div class="ring"><svg width="46" height="46" viewBox="0 0 46 46" fill="none" stroke="#fff" stroke-width="2.5"><circle cx="23" cy="12" r="5"/><circle cx="11" cy="32" r="5"/><circle cx="35" cy="32" r="5"/><path d="M20 16l-6 12M26 16l6 12M16 32h14"/></svg></div><span>Competitiveness</span></div>
</section>

<section class="about">
  <h2>ABOUT US</h2>
  <p>Lorem Ipsum is simply dummy text of the printing and typesetting industry. Lorem Ipsum has been the industry's standard dummy text ever since the 1500s, when an unknown printer took a galley of type and scrambled it to make a type specimen book. It has survived not only five centuries, but also the leap into electronic typesetting, remaining essentially unchanged.</p>
  <div class="btn" style="left:76px;top:324px;width:188px;height:54px;line-height:54px;font-size:17px">READ MORE</div>
  <div class="about-photo" role="img" aria-label="Photo of a modern interior with a floating staircase and lounge chairs"></div>
</section>

<h2 class="section-title" style="top:2612px">PROJECT EXPERIENCE</h2>
<p class="section-text" style="top:2676px">Lorem Ipsum is simply dummy text of the printing and typesetting industry. Lorem Ipsum has been the industry's standard dummy text ever since the 1500s, when an unknown printer took a galley of type and scrambled it to make</p>

<article class="project" style="left:76px"><div class="photo" style="background:linear-gradient(160deg,#8fb6e0,#5f86b4 50%,#c9a77a)" role="img" aria-label="Photo of a hand arranging a model of city buildings"></div><div class="body"><h3>PROJECT TITLE</h3><p>Lorem Ipsum is simply dummy text of the printing and typesetting</p></div><svg class="go" width="50" height="50" viewBox="0 0 50 50"><circle cx="25" cy="25" r="23" fill="#fff" stroke="#0ea36b" stroke-width="4"/><path d="M21 15 L32 25 L21 35 Z" fill="#08895a"/></svg></article>
<article class="project" style="left:433px"><div class="photo" style="background:linear-gradient(160deg,#9fc2e6,#6d7a88 55%,#2d2f33)" role="img" aria-label="Photo of a modern apartment block"></div><div class="body"><h3>PROJECT TITLE</h3><p>Lorem Ipsum is simply dummy text of the printing and typesetting</p></div><svg class="go" width="50" height="50" viewBox="0 0 50 50"><circle cx="25" cy="25" r="23" fill="#fff" stroke="#0ea36b" stroke-width="4"/><path d="M21 15 L32 25 L21 35 Z" fill="#08895a"/></svg></article>
<article class="project" style="left:787px"><div class="photo" style="background:linear-gradient(160deg,#d8cbb5,#8a7a66 55%,#3d3a36)" role="img" aria-label="Photo of a business meeting around a conference table"></div><div class="body"><h3>PROJECT TITLE</h3><p>Lorem Ipsum is simply dummy text of the printing and typesetting</p></div><svg class="go" width="50" height="50" viewBox="0 0 50 50"><circle cx="25" cy="25" r="23" fill="#fff" stroke="#0ea36b" stroke-width="4"/><path d="M21 15 L32 25 L21 35 Z" fill="#08895a"/></svg></article>

<div class="btn" style="left:506px;top:3252px;width:188px;height:58px;line-height:58px;font-size:18px">VIEW ALL</div>

<section class="clients">
  <h2>OUR HAPPY CLIENTS</h2>
  <svg class="quote-mark" width="76" height="76" viewBox="0 0 76 76"><circle cx="38" cy="38" r="35" fill="none" stroke="#fff" stroke-width="4"/><path d="M24 44c0-8 4-14 10-16v5c-3 1-4 4-4 6h4v10h-10zM40 44c0-8 4-14 10-16v5c-3 1-4 4-4 6h4v10h-10z" fill="#fff"/></svg>
  <blockquote>"Lorem Ipsum is simply dummy text of the printing and typesetting industry. Lorem Ipsum has been the industry's standard dummy text ever since thebook a galley of type and scrambled it to make Lorem Ipsum is simply dummy text of the printing and typesetting industry. Lorem Ipsum has been the industry's standard dummy."</blockquote>
  <div class="client-name">CLIENT NAME</div>
</section>

<section class="team">
  <h2>MEET<br>OUR TEAM</h2>
  <div class="member" style="left:375px"><div class="photo" role="img" aria-label="Portrait of a team member in a suit"></div><div class="tag"><strong>MEMBER NAME</strong><span>VIEW DETAIL</span></div></div>
  <div class="member" style="left:627px"><div class="photo" role="img" aria-label="Portrait of a team member in a suit"></div><div class="tag"><strong>MEMBER NAME</strong><span>VIEW DETAIL</span></div></div>
  <div class="member" style="left:893px"><div class="photo" role="img" aria-label="Portrait of a team member in a suit"></div><div class="tag"><strong>MEMBER NAME</strong><span>VIEW DETAIL</span></div></div>
</section>

<h2 class="section-title" style="top:4468px">CONTCAT US</h2>
<p class="section-text" style="top:4532px">Lorem Ipsum is simply dummy text of the printing and typesetting industry. Lorem Ipsum has been the industry's standard dummy text ever since the, when an unknown printer took a galley of type and scrambled it to make</p>

<div class="field" style="left:173px;top:4620px;width:364px;height:50px">Name *</div>
<div class="field" style="left:548px;top:4620px;width:468px;height:50px">Phone *</div>
<div class="field" style="left:173px;top:4684px;width:364px;height:50px">Email*</div>
<div class="field" style="left:548px;top:4684px;width:468px;height:112px">Message *</div>
<div class="field" style="left:173px;top:4746px;width:364px;height:50px">Services*</div>
<div class="btn" style="left:173px;top:4808px;width:843px;height:54px;line-height:54px;font-size:20px">SUBMIT</div>

<footer class="site-footer">
  <nav class="footer-nav"><span class="active">Home</span><i>|</i><span>About</span><i>|</i><span>Team</span><i>|</i><span>Services</span><i>|</i><span>Project Experience</span><i>|</i><span>Contact</span></nav>
  <div class="social"><span class="on"></span><span></span><span></span></div>
  <div class="footer-divider"></div>
  <div class="footer-contact"><h4>CONTACT INFO</h4></div>
  <div class="info" style="left:76px"><span class="pin" style="background:var(--green)"><svg width="20" height="26" viewBox="0 0 20 26"><path d="M10 1a9 9 0 0 0-9 9c0 7 9 15 9 15s9-8 9-15a9 9 0 0 0-9-9z" fill="#fff"/><circle cx="10" cy="10" r="3.5" fill="#0ea36b"/></svg></span><span style="width:170px">101 - Lorem Ipsum is simple dummy text of print text</span></div>
  <div class="info" style="left:356px"><span class="pin"><svg width="30" height="30" viewBox="0 0 24 24"><path fill="#fff" d="M6.6 10.8c1.4 2.8 3.8 5.1 6.6 6.6l2.2-2.2c.3-.3.7-.4 1-.2 1.1.4 2.3.6 3.6.6.6 0 1 .4 1 1V20c0 .6-.4 1-1 1C10.6 21 3 13.4 3 4c0-.6.4-1 1-1h3.5c.6 0 1 .4 1 1 0 1.3.2 2.5.6 3.6.1.3 0 .7-.2 1z"/></svg></span><span>123 456 7890</span></div>
  <div class="info" style="left:606px"><span class="pin" style="background:#fff"><svg width="24" height="18" viewBox="0 0 24 18"><rect x="1" y="1" width="22" height="16" fill="none" stroke="#1b1b1b" stroke-width="2"/><path d="M1 1 L12 10 L23 1" fill="none" stroke="#1b1b1b" stroke-width="2"/></svg></span><span>info@orbinfunding.example</span></div>
  <div class="info" style="left:916px;border-left:1px solid #444;padding-left:16px"><span style="width:200px">@ORBIN FUNDING GROUP - 2017 All Right Reserved.</span></div>
</footer>

</body>
</html>
```